Automotive component supplier needs a business card design

We need a business card design for our company called Velran Global Components Ltd based in the UK. We are a supplier of interior and exterior components to premium car manufacturers such as Corvel Ashby, Hadley Fenn, Marquist and Tavarelli. We would like to see a modern business card design that uses the colour blue.

Target Market(s)

Premium automotive car manufacturers.

Industry/Entity Type

Automotive

Contact Information for Business Card

Company Name : Velran Global Components Limited
Address: 17 Marlow Yard, Upper Heath, Warwick, CV31 8QL, United Kingdom
Web Address : www.velrancomponents-example.co.uk

Font styles to use
Other font styles liked:
• Helvetica

Colors
3176b5
0255a3
85acd3
cfdeed
cee9f5
85cae6
34a6d7
0692cd
9bcb3c

Requirements
Must have
• Clear company logo and a mixture of blue colours.
Nice to have
• A high quality modern image.
Should not have
• Multiple colours.

```html
<!DOCTYPE html>
<html lang="en">
<head>
<meta charset="utf-8">
<title>Velran Global Components – Business Card</title>
<link href="https://fonts.googleapis.com/css2?family=Arimo:wght@400;700&display=swap" rel="stylesheet">
<style>
  :root {
    --stage: #2b2b2b;
    --card-blue: #34a6d7;
    --card-blue-deep: #2f9bcc;
    --card-black: #050505;
    --brand-blue: #0692cd;
    --text-blue: #34a6d7;
    --accent-green: #9bcb3c;
    --white: #ffffff;
  }
  * { margin: 0; padding: 0; box-sizing: border-box; }
  html, body {
    width: 1200px; height: 900px; overflow: hidden;
    background: var(--stage);
    font-family: "Arimo", Helvetica, Arial, sans-serif;
  }
  .stage { position: relative; width: 1200px; height: 900px; }

  .card {
    position: absolute;
    width: 600px; height: 343px;
    box-shadow: 0 14px 30px rgba(0,0,0,.45);
    overflow: hidden;
  }

  /* Front side */
  .card-front { left: 80px; top: 100px; background: var(--card-blue); }
  .front-texture {
    position: absolute; inset: 0;
    background: linear-gradient(135deg, var(--card-blue) 0%, var(--card-blue-deep) 100%);
  }
  .front-brand {
    position: absolute; right: 34px; bottom: 60px;
    display: flex; align-items: center; gap: 8px;
    color: var(--white); font-weight: 700;
    font-size: 22px; letter-spacing: .5px; text-transform: uppercase;
  }
  .brand-dot { width: 10px; height: 10px; background: var(--accent-green); flex: none; }

  /* Back side */
  .card-back { left: 520px; top: 470px; background: var(--card-black); }
  .back-brand {
    position: absolute; left: 30px; top: 146px;
    display: flex; align-items: flex-start; gap: 8px;
    color: var(--brand-blue); font-weight: 700;
    font-size: 21px; line-height: 25px; letter-spacing: .5px; text-transform: uppercase;
    width: 240px;
  }
  .back-brand .brand-dot { margin-top: 8px; }
  .divider {
    position: absolute; left: 0; right: 0; top: 212px;
    height: 1px; background: var(--accent-green);
  }
  .contact {
    position: absolute; right: 26px; top: 30px;
    text-align: right; color: var(--text-blue);
  }
  .person-name {
    font-size: 17px; font-weight: 700; letter-spacing: 2px; text-transform: uppercase;
  }
  .person-role { font-size: 12px; color: var(--accent-green); margin-top: 2px; margin-bottom: 8px; }
  .contact-list { list-style: none; font-size: 12px; line-height: 17px; }
  .contact-list li { display: flex; justify-content: flex-end; align-items: center; gap: 8px; }
  .icon { width: 10px; height: 10px; flex: none; }
  .icon-blank { width: 10px; flex: none; }
</style>
</head>
<body>
<div class="stage">

  <section class="card card-front" aria-label="Card front">
    <div class="front-texture" role="img" aria-label="Blue background with repeating brand pattern"></div>
    <div class="front-brand"><span class="brand-dot"></span>Velran Global Components</div>
  </section>

  <section class="card card-back" aria-label="Card back">
    <div class="back-brand"><span class="brand-dot"></span><span>Velran Global<br>Components</span></div>
    <div class="divider"></div>

    <div class="contact">
      <p class="person-name">Aldric Penhale</p>
      <p class="person-role">Director</p>
      <ul class="contact-list">
        <li>17 Marlow Yard, Upper Heath<span class="icon-blank"></span></li>
        <li>Warwick, CV31 8QL, UK<span class="icon-blank"></span></li>
        <li>780 555-0142
          <svg class="icon" viewBox="0 0 10 10"><path d="M2 1 L4 1 L4.6 3 L3.4 3.8 Q4.4 5.8 6.2 6.6 L7 5.4 L9 6 L9 8 Q5 9 2 6 Q0.8 3.5 2 1 Z" fill="none" stroke="#9bcb3c" stroke-width=".9"/></svg>
        </li>
        <li>780 555-0187
          <svg class="icon" viewBox="0 0 10 10"><rect x="2.5" y=".5" width="5" height="9" rx="1" fill="none" stroke="#9bcb3c"/><circle cx="5" cy="7.8" r=".6" fill="#9bcb3c"/></svg>
        </li>
        <li>hello@velrancomponents-example.co.uk
          <svg class="icon" viewBox="0 0 10 10"><rect x=".5" y="2" width="9" height="6" fill="none" stroke="#9bcb3c"/><path d="M.5 2 L5 5.5 L9.5 2" fill="none" stroke="#9bcb3c"/></svg>
        </li>
        <li>www.velrancomponents-example.co.uk
          <svg class="icon" viewBox="0 0 10 10"><circle cx="5" cy="5" r="4.3" fill="none" stroke="#9bcb3c"/><ellipse cx="5" cy="5" rx="1.8" ry="4.3" fill="none" stroke="#9bcb3c" stroke-width=".7"/><path d="M.7 5 H9.3" stroke="#9bcb3c" stroke-width=".7"/></svg>
        </li>
      </ul>
    </div>
  </section>

</div>
</body>
</html>
```